Need A Standard Musical Download Website

We are looking for a talented designer to create a unique web design for our startup Music website called Vorde Sound.
The website should be responsive and filled with some creative stuffs along with bright colors.

Vorde sound is a website loaded with different types of music and capable of downloading the requested music by its users.
There will be categories of music which would be sorted by the genre. They include RnB, Hip-Hop, Afro pop, Pop, Dancehall and Reggae).

DESIGN STYLE/THEME

Creative, trendy, colorful, unique, and easy to use. You have freedom of selecting which ever color suits you. The design must be energetic and attractive.

NAVIGATION

HOME-MUSIC(RnB, Hip hop, Afro pop, POP, dancehall, Reggae)-ARTISTE-NEWS-LOGIN

PAGES REQUIRED
------------
1)Home Page
2)Music

FONTS
GOOGLE FONTS is strongly recommended.

Designers can get inspiration from https://tunabrook.example

Industry/Entity Type

Startup

```html
<!DOCTYPE html>
<html lang="en">
<head>
<meta charset="utf-8">
<title>Vorde Sound – Home</title>
<link rel="stylesheet" href="https://fonts.googleapis.com/css2?family=Montserrat:wght@400;500;600;700&family=Rye&display=swap">
<style>
:root{
  --ink:#0c0c12;
  --blue:#0d5e8a;
  --cyan:#27b6e0;
  --red:#d8333b;
  --peach:#f6a66e;
  --orange:#f47a20;
  --yellow:#f7b731;
  --grey-bg:#efefef;
  --text:#2a2a2a;
  --muted:#666;
  --white:#fff;
}
*{box-sizing:border-box;margin:0;padding:0}
html,body{width:727px;height:1200px;overflow:hidden;background:var(--white)}
body{font-family:"Montserrat",Arial,sans-serif;color:var(--text)}
.canvas{position:relative;width:727px;height:1200px;overflow:hidden}
.abs{position:absolute}
.heading{font-family:"Rye",Georgia,serif;font-weight:400;color:var(--blue);font-size:16px;letter-spacing:.5px;white-space:nowrap}
.heading::after{content:"";display:block;height:1px;background:#9bb9cc;margin-top:3px}

/* header */
.site-header{position:absolute;left:0;top:0;width:727px;height:39px;background:var(--ink)}
.brand{position:absolute;display:flex;align-items:center;gap:4px;color:var(--white);font-weight:700;font-size:14px}
.brand-dot{width:7px;height:7px;border-radius:50%;background:var(--cyan)}
.main-nav{position:absolute;left:331px;top:15px;display:flex;gap:11px;font-size:6.5px;font-weight:700;color:#ddd;letter-spacing:.3px}
.main-nav .active{color:var(--orange)}
.search{position:absolute;left:483px;top:11px;width:109px;height:16px;border:1px solid #444;border-radius:8px;font-size:5.5px;color:#777;padding:4px 8px;background:#111}
.search::after{content:"";position:absolute;right:-1px;top:-1px;width:16px;height:16px;border-radius:0 8px 8px 0;background:#555}
.login-btn{position:absolute;left:599px;top:11px;width:41px;height:16px;border-radius:8px;background:var(--blue);color:var(--white);font-size:6.5px;font-weight:700;text-align:center;line-height:16px}

/* hero */
.hero{position:absolute;left:0;top:39px;width:727px;height:224px;background:radial-gradient(ellipse at 70% 40%,#3a2fb8 0%,#2a1b8f 40%,#241060 75%,#1a0a3e 100%)}
.hero-title{left:87px;top:30px;font-family:"Rye",Georgia,serif;font-weight:400;font-size:18px;color:var(--peach);letter-spacing:1px}
.hero-panel{left:87px;top:59px;width:218px;height:96px;background:rgba(20,8,50,.55)}
.hero-row{position:absolute;left:10px;width:198px;height:28px;display:flex;align-items:center;font-size:7px;font-weight:600;color:var(--white);border-bottom:1px solid rgba(255,255,255,.25)}
.hero-row span:first-child{width:37px;border-right:1px solid rgba(255,255,255,.25);height:100%;display:flex;align-items:center}
.hero-row span:last-child{padding-left:12px}
.hero-action{position:absolute;top:70px;display:flex;align-items:center;gap:5px;font-size:5.5px;font-weight:700;color:var(--cyan);line-height:1.1}
.hero-action .icon-disc{width:16px;height:16px;border-radius:50%;background:var(--cyan);display:flex;align-items:center;justify-content:center}
.player{left:340px;top:25px;width:300px;height:148px;background:linear-gradient(110deg,#efe0cf 0%,#e8cdb0 40%,#a66b44 70%,#5a3424 100%)}
.play{position:absolute;border-radius:50%;border:2px solid var(--white);display:flex;align-items:center;justify-content:center}
.play::after{content:"";border-left:9px solid var(--white);border-top:6px solid transparent;border-bottom:6px solid transparent;margin-left:3px}
.arrow-btn{position:absolute;top:184px;width:22px;height:22px;border-radius:50%;display:flex;align-items:center;justify-content:center}

.band{position:absolute;left:0;width:727px}

/* songs */
.song-card{position:absolute;width:110px}
.song-art{height:85px;position:relative}
.song-art .play{left:40px;top:28px;width:30px;height:30px}
.song-art .play::after{border-left-width:7px;border-top-width:5px;border-bottom-width:5px}
.song-meta{position:relative;height:28px;background:var(--white);border:1px solid #e3b9bb;border-top:0;padding:7px 0 0 9px}
.song-meta.short{height:24px;padding-top:5px}
.song-title{font-size:7px;font-weight:600;color:var(--text)}
.song-artist{font-size:5px;color:var(--muted);margin-top:1px}
.song-tools{position:absolute;right:-1px;top:0;width:17px;height:28px;background:var(--red)}
.song-tools svg{display:block}
.view-all{position:absolute;font-size:6.5px;font-weight:700;color:var(--blue);letter-spacing:.3px}

/* artists */
.artist-card{position:absolute;top:678px;width:110px}
.artist-photo{height:85px}
.artist-name{height:29px;border:1px solid #e3b9bb;border-top:0;font-size:7.5px;font-weight:500;text-align:center;line-height:29px;color:var(--text)}
.dots{position:absolute;left:356px;top:811px;display:flex;gap:5px}
.dots i{width:5px;height:5px;background:#ccc;display:block}
.dots i.on{background:var(--blue)}

/* grey strip */
.latest{position:absolute;left:0;top:836px;width:727px;height:216px;background:var(--grey-bg)}
.track-list{position:absolute;list-style:none;font-size:7.5px;color:var(--text)}
.track-list li{height:16px;display:flex;align-items:center;gap:5px;white-space:nowrap}
.track-list li::before{content:"";width:5px;height:5px;border:1px solid var(--cyan);display:block}
.news-item{position:absolute;display:flex;gap:6px;width:135px}
.news-thumb{width:38px;height:31px;flex:none}
.news-text{font-size:7.5px;line-height:1.15;color:var(--text)}
.news-date{font-size:5.5px;color:var(--muted);margin-top:2px}

/* footer */
.site-footer{position:absolute;left:0;top:1053px;width:727px;height:117px;background:linear-gradient(90deg,#4a1a7a 0%,#3b1f8a 55%,#22228c 100%)}
.social{position:absolute;top:59px;width:11px;height:11px;border-radius:50%}
.foot-links{position:absolute;top:38px;list-style:none;font-size:6px;font-weight:700;color:#e6e6f5;letter-spacing:.3px}
.foot-links li{height:12px}
.news-label{position:absolute;left:512px;top:38px;font-size:6px;font-weight:700;color:#e6e6f5;letter-spacing:.3px}
.email{position:absolute;left:512px;top:51px;width:128px;height:21px;background:var(--white);font-size:6px;color:#555;padding:7px 6px}
.submit{position:absolute;left:512px;top:77px;width:45px;height:15px;background:var(--blue);color:#bfe4f5;font-size:7px;font-weight:700;text-align:center;line-height:15px}
.legal{position:absolute;left:0;top:1170px;width:727px;height:30px;background:#141414;font-size:6px;color:#888;text-align:center;line-height:30px;letter-spacing:.3px}
</style>
</head>
<body>
<svg width="0" height="0" style="position:absolute" aria-hidden="true">
  <defs>
    <symbol id="tools" viewBox="0 0 17 28">
      <path d="M8.5 11 L4.6 7.2 A2.1 2.1 0 0 1 8.5 4.6 A2.1 2.1 0 0 1 12.4 7.2 Z" fill="#fff"/>
      <line x1="3" y1="14" x2="14" y2="14" stroke="#fff" stroke-opacity=".55" stroke-width=".6"/>
      <path d="M8.5 16.5 V22 M6.3 20 L8.5 22.2 L10.7 20" fill="none" stroke="#fff" stroke-width="1" stroke-linecap="round" stroke-linejoin="round"/>
      <path d="M4.8 21.5 V24 H12.2 V21.5" fill="none" stroke="#fff" stroke-width="1"/>
    </symbol>
    <symbol id="heart" viewBox="0 0 10 10">
      <path d="M5 8.6 L1.6 5.2 A2.1 2.1 0 0 1 5 2.6 A2.1 2.1 0 0 1 8.4 5.2 Z" fill="#fff"/>
    </symbol>
    <symbol id="download" viewBox="0 0 10 10">
      <path d="M5 1.5 V6.5 M3 4.6 L5 6.6 L7 4.6" fill="none" stroke="#fff" stroke-width="1" stroke-linecap="round" stroke-linejoin="round"/>
      <path d="M1.8 6 V8.5 H8.2 V6" fill="none" stroke="#fff" stroke-width="1"/>
    </symbol>
  </defs>
</svg>
<div class="canvas">

  <header class="site-header">
    <div class="brand" style="left:87px;top:11px"><span class="brand-dot"></span>Vorde Sound</div>
    <nav class="main-nav"><span class="active">HOME</span><span>MUSIC</span><span>ARTISTS</span><span>NEWS</span></nav>
    <div class="search">SEARCH</div>
    <div class="login-btn">LOGIN</div>
  </header>

  <section class="hero">
    <h1 class="abs hero-title">TRENDING NOW!</h1>
    <div class="abs hero-panel">
      <div class="hero-row" style="top:0"><span>ALBUM</span><span>ROCK &amp; ROLL 2017 - RELOADED</span></div>
      <div class="hero-row" style="top:28px"><span>ARTIST</span><span>ROWAN PIKE</span></div>
      <div class="hero-action" style="left:12px"><span class="icon-disc"><svg width="10" height="10"><use href="#heart"/></svg></span><span>ADD TO<br>FAVOURITES</span></div>
      <div class="hero-action" style="left:92px"><span class="icon-disc"><svg width="10" height="10"><use href="#download"/></svg></span><span>DOWNLOAD<br>NOW</span></div>
    </div>
    <div class="abs player" role="img" aria-label="Album artwork: rock singer in sunglasses shouting into a microphone">
      <div class="play" style="left:139px;top:49px;width:46px;height:46px"></div>
    </div>
    <div class="arrow-btn" style="left:478px;background:var(--blue)"><svg width="9" height="9" viewBox="0 0 9 9"><path d="M2 1.5 V7.5 M7 1.5 L3.5 4.5 L7 7.5" fill="none" stroke="#fff" stroke-width="1.2"/></svg></div>
    <div class="arrow-btn" style="left:504px;background:var(--cyan)"><svg width="9" height="9" viewBox="0 0 9 9"><path d="M7 1.5 V7.5 M2 1.5 L5.5 4.5 L2 7.5" fill="none" stroke="#fff" stroke-width="1.2"/></svg></div>
  </section>

  <svg class="band" style="top:262px" width="727" height="40" viewBox="0 0 727 40" aria-hidden="true">
    <defs><linearGradient id="warm" x1="0" x2="1"><stop offset="0" stop-color="#e8322a"/><stop offset=".55" stop-color="#f47a20"/><stop offset="1" stop-color="#f7b731"/></linearGradient></defs>
    <polygon points="0,0 727,0 727,12 640,38 0,6" fill="url(#warm)"/>
  </svg>

  <h2 class="abs heading" style="left:87px;top:291px">TOP 10 SONGS</h2>

  <!-- row 1 -->
  <div class="song-card" style="left:87px;top:332px"><div class="song-art" role="img" aria-label="Song cover: performer in a white suit on a red stage" style="background:linear-gradient(135deg,#7a1a1a,#c9443a 50%,#e6d6c8)"><div class="play"></div></div><div class="song-meta"><div class="song-title">PAPER SKYLINES</div><div class="song-artist">Ivo Marsh</div><div class="song-tools"><svg width="17" height="28"><use href="#tools"/></svg></div></div></div>
  <div class="song-card" style="left:197px;top:332px"><div class="song-art" role="img" aria-label="Song cover: violinist in a pink dress" style="background:linear-gradient(135deg,#c9a07a,#b25a6a 50%,#5a3a4a)"><div class="play"></div></div><div class="song-meta short"><div class="song-title">PAPER SKYLINES</div><div class="song-artist">Ivo Marsh</div><div class="song-tools"><svg width="17" height="28"><use href="#tools"/></svg></div></div></div>
  <div class="song-card" style="left:307px;top:332px"><div class="song-art" role="img" aria-label="Song cover: friends in a convertible at sunset" style="background:linear-gradient(160deg,#f2b24a,#c76a2a 55%,#6a3a22)"><div class="play"></div></div><div class="song-meta"><div class="song-title">PAPER SKYLINES</div><div class="song-artist">Ivo Marsh</div><div class="song-tools"><svg width="17" height="28"><use href="#tools"/></svg></div></div></div>
  <div class="song-card" style="left:418px;top:332px"><div class="song-art" role="img" aria-label="Song cover: guitarist with flying hair" style="background:linear-gradient(135deg,#4a3a30,#b08a50 50%,#5a4a3a)"><div class="play"></div></div><div class="song-meta short"><div class="song-title">PAPER SKYLINES</div><div class="song-artist">Ivo Marsh</div><div class="song-tools"><svg width="17" height="28"><use href="#tools"/></svg></div></div></div>
  <div class="song-card" style="left:529px;top:332px"><div class="song-art" role="img" aria-label="Song cover: couple posing together" style="background:linear-gradient(135deg,#2a3a5a,#7a5a7a 50%,#d0a08a)"><div class="play"></div></div><div class="song-meta"><div class="song-title">PAPER SKYLINES</div><div class="song-artist">Ivo Marsh</div><div class="song-tools"><svg width="17" height="28"><use href="#tools"/></svg></div></div></div>

  <!-- row 2 -->
  <div class="song-card" style="left:87px;top:460px"><div class="song-art" role="img" aria-label="Song cover: friends in a convertible at sunset" style="background:linear-gradient(160deg,#f2b24a,#c76a2a 55%,#6a3a22)"><div class="play"></div></div><div class="song-meta"><div class="song-title">PAPER SKYLINES</div><div class="song-artist">Ivo Marsh</div><div class="song-tools"><svg width="17" height="28"><use href="#tools"/></svg></div></div></div>
  <div class="song-card" style="left:197px;top:460px"><div class="song-art" role="img" aria-label="Song cover: couple posing together" style="background:linear-gradient(135deg,#2a3a5a,#7a5a7a 50%,#d0a08a)"><div class="play"></div></div><div class="song-meta short"><div class="song-title">PAPER SKYLINES</div><div class="song-artist">Ivo Marsh</div><div class="song-tools"><svg width="17" height="28"><use href="#tools"/></svg></div></div></div>
  <div class="song-card" style="left:307px;top:460px"><div class="song-art" role="img" aria-label="Song cover: guitarist with flying hair" style="background:linear-gradient(135deg,#4a3a30,#b08a50 50%,#5a4a3a)"><div class="play"></div></div><div class="song-meta"><div class="song-title">PAPER SKYLINES</div><div class="song-artist">Ivo Marsh</div><div class="song-tools"><svg width="17" height="28"><use href="#tools"/></svg></div></div></div>
  <div class="song-card" style="left:418px;top:460px"><div class="song-art" role="img" aria-label="Song cover: performer in a white suit on a red stage" style="background:linear-gradient(135deg,#7a1a1a,#c9443a 50%,#e6d6c8)"><div class="play"></div></div><div class="song-meta short"><div class="song-title">PAPER SKYLINES</div><div class="song-artist">Ivo Marsh</div><div class="song-tools"><svg width="17" height="28"><use href="#tools"/></svg></div></div></div>
  <div class="song-card" style="left:529px;top:460px"><div class="song-art" role="img" aria-label="Song cover: violinist in a pink dress" style="background:linear-gradient(135deg,#c9a07a,#b25a6a 50%,#5a3a4a)"><div class="play"></div></div><div class="song-meta"><div class="song-title">PAPER SKYLINES</div><div class="song-artist">Ivo Marsh</div><div class="song-tools"><svg width="17" height="28"><use href="#tools"/></svg></div></div></div>

  <div class="view-all" style="left:575px;top:587px">VIEW ALL SONGS &rarr;</div>
  <div class="abs" style="left:87px;top:613px;width:553px;border-top:1px dotted #8fb4c9"></div>

  <h2 class="abs heading" style="left:299px;top:634px">TOP 10 ARTISTS</h2>

  <div class="artist-card" style="left:87px"><div class="artist-photo" role="img" aria-label="Artist portrait on a peach background" style="background:linear-gradient(180deg,#f6c99a,#e3a46a)"></div><div class="artist-name">LENNA GREY</div></div>
  <div class="artist-card" style="left:197px"><div class="artist-photo" role="img" aria-label="Black and white artist portrait" style="background:linear-gradient(180deg,#5a5a5a,#2a2a2a)"></div><div class="artist-name" style="height:25px;line-height:25px">TAVO REYES</div></div>
  <div class="artist-card" style="left:307px"><div class="artist-photo" role="img" aria-label="Black and white artist portrait" style="background:linear-gradient(180deg,#bdbdbd,#8a8a8a)"></div><div class="artist-name">MIRA KELL</div></div>
  <div class="artist-card" style="left:418px"><div class="artist-photo" role="img" aria-label="Black and white artist portrait" style="background:linear-gradient(180deg,#6a6a6a,#3a3a3a)"></div><div class="artist-name" style="height:25px;line-height:25px">CALEB STONE</div></div>
  <div class="artist-card" style="left:529px"><div class="artist-photo" role="img" aria-label="Black and white artist portrait" style="background:linear-gradient(180deg,#d6d6d6,#a8a8a8)"></div><div class="artist-name">JUNO HART</div></div>

  <div class="dots"><i class="on"></i><i></i></div>
  <div class="view-all" style="left:572px;top:810px">VIEW ALL ARTISTS &rarr;</div>

  <section class="latest">
    <h2 class="abs heading" style="left:87px;top:32px">LATEST MP3 TRACKS</h2>
    <ul class="track-list" style="left:87px;top:65px">
      <li>Weekend Songs 2016</li><li>Kade Ft. Nori Vale - Glow</li><li>Tribeline - Late and loud</li><li>Caleb Stone - I Could Be</li><li>Omari - This Road Is Our Road</li>
    </ul>
    <ul class="track-list" style="left:229px;top:65px">
      <li>Omari - Hold U Down</li><li>Rook Ft. Lil Tenn - Swerve</li><li>Tribeline - Call Waiting</li><li>Delia Rae - Pillow Party</li><li>Marcus Vale - 100 Wayz</li>
    </ul>
    <div class="view-all" style="left:314px;top:160px">VIEW ALL &rarr;</div>

    <h2 class="abs heading" style="left:370px;top:32px">LATEST NEWS</h2>
    <div class="news-item" style="left:370px;top:69px"><div class="news-thumb" role="img" aria-label="News photo: singer in sunglasses" style="background:linear-gradient(135deg,#e0c49a,#8a5a3a)"></div><div><div class="news-text">Lorem ipsum dolor sit amet dueo</div><div class="news-date">01/02/2017</div></div></div>
    <div class="news-item" style="left:370px;top:106px"><div class="news-thumb" role="img" aria-label="News photo: concert crowd under stage lights" style="background:linear-gradient(135deg,#f2b24a,#2a1a3a)"></div><div><div class="news-text">Lorem ipsum dolor sit amet dueo</div><div class="news-date">01/02/2017</div></div></div>
    <div class="news-item" style="left:512px;top:69px"><div class="news-thumb" role="img" aria-label="News photo: guitarist on stage" style="background:linear-gradient(135deg,#c98a5a,#3a2a3a)"></div><div><div class="news-text">Lorem ipsum dolor sit amet dueo</div><div class="news-date">01/02/2017</div></div></div>
    <div class="news-item" style="left:512px;top:106px"><div class="news-thumb" role="img" aria-label="News photo: rock singer shouting" style="background:linear-gradient(135deg,#5aa0c0,#8a4a3a)"></div><div><div class="news-text">Lorem ipsum dolor sit amet dueo</div><div class="news-date">01/02/2017</div></div></div>
    <div class="view-all" style="left:601px;top:160px">VIEW ALL &rarr;</div>
  </section>

  <svg class="band" style="top:1013px" width="727" height="41" viewBox="0 0 727 41" aria-hidden="true">
    <defs><linearGradient id="warm2" x1="0" x2="1"><stop offset="0" stop-color="#f7b731"/><stop offset=".5" stop-color="#f47a20"/><stop offset="1" stop-color="#e8322a"/></linearGradient></defs>
    <polygon points="0,26 88,0 727,24 727,41 0,41" fill="url(#warm2)"/>
  </svg>

  <footer class="site-footer">
    <div class="brand" style="left:87px;top:36px"><span class="brand-dot"></span>Vorde Sound</div>
    <span class="social" style="left:118px;background:#3b5bb0"></span>
    <span class="social" style="left:133px;background:#2fa8e0"></span>
    <span class="social" style="left:148px;background:#d8333b"></span>
    <ul class="foot-links" style="left:273px"><li>HOME</li><li>MUSIC</li><li>ARTISTS</li><li>NEWS</li></ul>
    <ul class="foot-links" style="left:399px"><li>LOGIN</li><li>MY ACCOUNT</li><li>PRIVACY</li><li>CONTACT</li></ul>
    <div class="news-label">NEWSLETTER SIGNUP</div>
    <div class="email">Email Address</div>
    <div class="submit">SUBMIT</div>
  </footer>
  <div class="legal">&copy; VORDE SOUND | ALL RIGHTS RESERVED</div>

</div>
</body>
</html>
```